ADA COMPLIANCE

We are in need of flyer or tri fold page for ada compliance, handicap ramps and parking lot striping.

Target Market(s)

Commercial Construction Industry

Industry/Entity Type

Parking

Font styles to use
Other font styles liked:
• Felix Titling

Colors
0355a3
acd036

Requirements
Must have
• Our Company Name and logo, 8005172934 number License #2847306
• List of services provided in uploaded images. Navy blue with high vizability green

```html
<!DOCTYPE html>
<html lang="en">
<head>
<meta charset="utf-8">
<title>Summit Build Services – ADA Compliance Tri-fold</title>
<link href="https://fonts.googleapis.com/css2?family=Lato:wght@400;700;900&family=Oswald:wght@300;500&display=swap" rel="stylesheet">
<style>
:root{
  --navy:#27467f;
  --navy-deep:#1f3a6d;
  --green:#a8cb3a;
  --green-light:#c6df6a;
  --sky:#3fb4e6;
  --asphalt:#3a4656;
  --paper:#ffffff;
  --mist:#eef0f3;
  --stage:#e9eaec;
}
*{margin:0;padding:0;box-sizing:border-box}
html,body{width:1200px;height:898px;overflow:hidden;background:var(--stage)}
.brochure{position:absolute;left:60px;top:30px;width:1080px;height:838px;display:flex;box-shadow:0 10px 30px rgba(0,0,0,.18)}
.panel{position:relative;width:360px;height:838px;overflow:hidden;background:var(--paper)}
.panel+.panel{border-left:1px solid rgba(0,0,0,.06)}
.panel svg.bg{position:absolute;inset:0}
.photo{position:absolute}
.brand{position:absolute;font-family:"Lato",sans-serif;font-weight:900;color:var(--navy);letter-spacing:1px;display:flex;align-items:center;gap:8px}
.brand .mark{width:14px;height:14px;background:var(--navy)}

/* services panel */
.services .brand{left:95px;top:92px;font-size:19px}
.services .tagline{position:absolute;left:22px;top:150px;width:320px;background:var(--navy);color:#fff;font:italic 700 12px "Lato",sans-serif;padding:6px 10px;letter-spacing:.3px}
.service-list{position:absolute;top:190px;list-style:none;font:400 13.5px/20px "Lato",sans-serif;color:var(--navy)}
.service-list li::before{content:"•";margin-right:6px}
.service-list li.key{font-weight:700}
.service-list.col-a{left:28px}
.service-list.col-b{left:200px}

/* contact panel */
.badge{position:absolute;left:120px;top:330px;width:120px;height:134px}
.contact{position:absolute;left:0;right:0;top:510px;text-align:center;color:var(--navy);font-family:"Lato",sans-serif}
.contact .cta{font-size:24px;font-weight:400;letter-spacing:-.5px}
.contact .phone{font-size:30px;font-weight:900;letter-spacing:-1px;margin-top:2px}
.contact .email{font-size:16px;font-weight:700;margin-top:6px}
.contact .web{font-size:15px;font-weight:700;letter-spacing:6px;margin-top:6px}
.contact .license{font-size:15px;font-weight:700;letter-spacing:1px;margin-top:10px}

/* cover panel */
.cover .brand{left:0;right:0;justify-content:center;top:70px;font-size:22px}
.cover .headline{position:absolute;left:0;right:0;top:540px;text-align:center;color:var(--navy);font-family:"Oswald",sans-serif}
.cover .headline .lead{font-weight:300;font-size:30px}
.cover .headline .focus{font-weight:500;font-size:21px;margin-top:2px}
.cover .web{font:700 15px "Lato",sans-serif;letter-spacing:6px;margin-top:12px}
</style>
</head>
<body>
<main class="brochure">

  <section class="panel services">
    <svg class="bg" width="360" height="838" viewBox="0 0 360 838">
      <defs><linearGradient id="mistFade" x1="0" y1="0" x2="0" y2="1"><stop offset="0" stop-color="#e3e6ea"/><stop offset="1" stop-color="#fafafa"/></linearGradient></defs>
      <rect width="360" height="838" fill="url(#mistFade)"/>
      <polygon points="0,0 360,0 360,18 0,95" fill="var(--green)"/>
      <polygon points="0,0 230,0 0,70" fill="var(--navy)"/>
      <polygon points="0,540 360,600 360,630 0,560" fill="var(--green)"/>
      <polygon points="0,800 360,760 360,838 0,838" fill="var(--navy)"/>
    </svg>
    <div class="brand"><span class="mark"></span>SUMMIT</div>
    <div class="tagline">There is nothing we cannot do, but we specialize in:</div>
    <ul class="service-list col-a">
      <li class="key">ADA Ramps,</li><li>New Construction,</li><li>Tenant Improvement,</li><li>Building Alterations,</li><li>Design/Build,</li><li>Retail,</li><li>Hotel,</li><li>Casinos,</li><li>Fueling Stations</li><li>Shopping Malls,</li><li>Auto Facilities,</li><li>Financial Institutions,</li><li>Parking Structures,</li>
    </ul>
    <ul class="service-list col-b">
      <li class="key">Lot Striping,</li><li>Electrical,</li><li>Plumbing,</li><li>Flooring,</li><li>ADA Improvements</li><li>/Modifications,</li><li>Drywall,</li><li>Painting,</li><li>Restaurants,</li><li>Custom Concrete,</li><li>Foundations,</li><li>Framing,</li><li>Roofing...And MORE</li>
    </ul>
    <svg class="photo" style="left:0;top:560px" width="360" height="240" viewBox="0 0 360 240" role="img" aria-label="Photo of a freshly striped parking lot with crosswalk lines beside event tents and a delivery truck">
      <defs><linearGradient id="lotA" x1="0" y1="0" x2="0" y2="1"><stop offset="0" stop-color="#8fb7e0"/><stop offset=".45" stop-color="#5a6f8c"/><stop offset="1" stop-color="var(--asphalt)"/></linearGradient></defs>
      <polygon points="0,0 360,70 360,200 0,240" fill="url(#lotA)"/>
    </svg>
  </section>

  <section class="panel contact-panel">
    <svg class="bg" width="360" height="838" viewBox="0 0 360 838">
      <defs>
        <linearGradient id="lotB" x1="0" y1="0" x2="0" y2="1"><stop offset="0" stop-color="#c9d3dc"/><stop offset=".4" stop-color="#56657a"/><stop offset="1" stop-color="#2e3b4c"/></linearGradient>
        <linearGradient id="greenField" x1="0" y1="0" x2="0" y2="1"><stop offset="0" stop-color="var(--green-light)"/><stop offset="1" stop-color="var(--green)"/></linearGradient>
      </defs>
      <rect width="360" height="838" fill="url(#greenField)"/>
      <polygon points="0,0 360,0 360,20 0,70" fill="var(--navy)"/>
      <polygon points="0,395 360,360 360,378 0,413" fill="var(--navy)"/>
      <polygon points="0,775 360,740 360,838 0,838" fill="var(--navy)"/>
    </svg>
    <svg class="photo" style="left:0;top:0" width="360" height="400" viewBox="0 0 360 400" role="img" aria-label="Photo of accessible parking stalls with blue wheelchair symbols painted on asphalt">
      <polygon points="0,70 360,20 360,360 0,395" fill="url(#lotB)"/>
    </svg>
    <svg class="badge" viewBox="0 0 120 134" aria-label="Accessibility symbol">
      <polygon points="60,3 115,33 115,101 60,131 5,101 5,33" fill="var(--navy)"/>
      <polygon points="60,13 106,38 106,96 60,121 14,96 14,38" fill="#fff"/>
      <circle cx="56" cy="32" r="7" fill="var(--navy)"/>
      <path d="M54 42 L56 70 L78 70 L88 94" fill="none" stroke="var(--navy)" stroke-width="7" stroke-linecap="round" stroke-linejoin="round"/>
      <path d="M44 58 A22 22 0 1 0 76 88" fill="none" stroke="var(--navy)" stroke-width="6" stroke-linecap="round"/>
    </svg>
    <div class="contact">
      <div class="cta">CALL US NOW:</div>
      <div class="phone">+1 800 517 2934</div>
      <div class="email">E-mail: info@summitbs.com</div>
      <div class="web">www.summitbs.com</div>
      <div class="license">License #2847306</div>
    </div>
  </section>

  <section class="panel cover">
    <svg class="bg" width="360" height="838" viewBox="0 0 360 838">
      <defs><linearGradient id="lotC" x1="0" y1="0" x2="0" y2="1"><stop offset="0" stop-color="#f2f4f6"/><stop offset=".35" stop-color="#6f7d92"/><stop offset="1" stop-color="#34415a"/></linearGradient></defs>
      <rect width="360" height="838" fill="var(--paper)"/>
      <polygon points="0,0 360,0 360,10 0,30" fill="var(--green)"/>
      <polygon points="0,470 360,430 360,470 0,500" fill="var(--green)"/>
      <polygon points="0,490 360,455 360,470 0,505" fill="var(--navy)"/>
      <polygon points="0,780 360,720 360,838 0,838" fill="var(--navy)"/>
    </svg>
    <svg class="photo" style="left:0;top:0" width="360" height="500" viewBox="0 0 360 500" role="img" aria-label="Photo of a row of accessible parking stalls with bright blue wheelchair symbols and no-parking striping">
      <polygon points="0,30 360,10 360,455 0,490" fill="url(#lotC)"/>
    </svg>
    <div class="brand"><span class="mark"></span>SUMMIT</div>
    <div class="headline">
      <div class="lead">We set new standards for</div>
      <div class="focus">Design, Quality and Craftsmanship</div>
      <div class="web">www.summitbs.com</div>
    </div>
  </section>

</main>
</body>
</html>
```